Stonebrace Business Card Design

The Stonebrace Co is an aggregate (crushing) equipment dealer serving Western Canadian provinces. Stonebrace is a distributor of aggregate equipment for different manufacturers.

We are looking to change and update the existing business card which has been used since the existence of the company. A copy of existing card has been attached for reference. The Stonebrace Co logo we want to remain the same and we want the green color to remain the same.

We are wanting something new with a different look. A refreshing card to show a new modern and updated look. No longer wanting to have the manufacturers on the back of the card but something more like our logo on the back of the card with a statement like "Crushing Solutions"

ideas could be:
- card can be different colors on front and back
- front or reverse of the card could possibly be the green color with the logo in black

Target Market(s)

Owners of Aggregate/Crushing companies

Contact Information for Business Card

see above

Requirements
Must have
• - logo to remain same along with same font within logo
• - green color to remain same
Nice to have
• as noted above under project description
Should not have

```html
<!DOCTYPE html>
<html lang="en">
<head>
<meta charset="utf-8">
<title>Stonebrace Business Card</title>
<link rel="stylesheet" href="https://fonts.googleapis.com/css2?family=Arimo:wght@400;700&display=swap">
<style>
  :root {
    --backdrop: #979797;
    --brand-green: #8a8d08;
    --name-green: #7c8a0f;
    --ink: #1c1c1c;
    --paper: #ffffff;
  }
  * { margin: 0; padding: 0; box-sizing: border-box; }
  html, body { width: 1200px; height: 900px; overflow: hidden; }
  body {
    background: var(--backdrop);
    font-family: "Arimo", Arial, sans-serif;
    position: relative;
  }
  .card {
    position: absolute;
    top: 306px;
    width: 440px;
    height: 272px;
    overflow: hidden;
  }
  .card-front { left: 149px; background: var(--paper); }
  .card-back { left: 608px; background: var(--brand-green); }

  .name-tab { position: absolute; left: 0; top: 26px; }
  .holder-name {
    position: absolute; left: 37px; top: 39px;
    font-size: 15.5px; color: var(--name-green); letter-spacing: 0.2px;
  }

  .brand-dot {
    position: absolute; left: 276px; top: 78px;
    width: 42px; height: 42px; border-radius: 50%;
    background: var(--brand-green);
  }
  .company-name {
    position: absolute; right: 24px; top: 146px;
    font-size: 18px; font-weight: 700; color: var(--ink); letter-spacing: 0.1px;
  }

  .contact-list {
    position: absolute; left: 28px; top: 167px;
    list-style: none; font-size: 12.5px; color: var(--ink);
  }
  .contact-list li { display: flex; align-items: center; height: 15.8px; }
  .contact-list svg { width: 10px; height: 10px; margin-right: 6px; flex: none; }

  .address {
    position: absolute; right: 25px; top: 212px;
    text-align: right; font-size: 12.5px; line-height: 16px; color: var(--ink);
  }
  .footer-band { position: absolute; left: 0; bottom: 0; }

  .back-wordmark {
    position: absolute; left: 0; right: 0; top: 104px;
    display: flex; align-items: center; justify-content: center; gap: 14px;
    color: var(--paper); font-size: 26px; font-weight: 700;
  }
  .back-wordmark .brand-dot-light {
    width: 34px; height: 34px; border-radius: 50%; background: var(--paper);
  }
  .tagline {
    position: absolute; left: 0; right: 0; top: 220px;
    text-align: center; color: var(--paper);
    font-size: 13px; font-weight: 700; letter-spacing: 1.2px;
  }
</style>
</head>
<body>
  <section class="card card-front">
    <svg class="name-tab" width="30" height="36" viewBox="0 0 30 36">
      <polygon points="0,0 11,0 17,36 0,36" fill="var(--ink)"/>
      <polygon points="13,0 28,0 28,36 19,36" fill="var(--brand-green)"/>
    </svg>
    <div class="holder-name">DALE MORVEN</div>

    <div class="brand-dot"></div>
    <div class="company-name">THE STONEBRACE CO.</div>

    <ul class="contact-list">
      <li><svg viewBox="0 0 10 10"><path d="M1 3 Q5 0 9 3 L8 4.5 L6.5 3.8 L6.5 3 Q5 2.5 3.5 3 L3.5 3.8 L2 4.5 Z M2 5 H8 L9 9 H1 Z" fill="var(--brand-green)"/></svg>780.555.0142(Direct)</li>
      <li><svg viewBox="0 0 10 10"><path d="M1 3 Q5 0 9 3 L8 4.5 L6.5 3.8 L6.5 3 Q5 2.5 3.5 3 L3.5 3.8 L2 4.5 Z M2 5 H8 L9 9 H1 Z" fill="var(--brand-green)"/></svg>780.555.0187</li>
      <li><svg viewBox="0 0 10 10"><rect x="2.5" y="0.5" width="5" height="3" fill="var(--brand-green)"/><rect x="1" y="4" width="8" height="5.5" fill="var(--brand-green)"/><rect x="3" y="5.5" width="4" height="1" fill="#fff"/></svg>780.555.0199</li>
      <li><svg viewBox="0 0 10 10"><rect x="0.5" y="2" width="9" height="6.5" fill="var(--brand-green)"/><path d="M0.5 2 L5 5.8 L9.5 2" stroke="#fff" stroke-width="0.9" fill="none"/></svg>dale@stonebr.com</li>
      <li><svg viewBox="0 0 10 10"><circle cx="5" cy="5" r="4.5" fill="var(--brand-green)"/><path d="M0.5 5 H9.5 M5 0.5 Q2.5 5 5 9.5 M5 0.5 Q7.5 5 5 9.5" stroke="#fff" stroke-width="0.7" fill="none"/></svg>www.stonebrace.ca</li>
    </ul>

    <div class="address">2215-48B Avenue<br>Brookvale, Alberta T4X 2K8</div>

    <svg class="footer-band" width="440" height="20" viewBox="0 0 440 20">
      <polygon points="0,6 217,6 206,20 0,20" fill="var(--ink)"/>
      <polygon points="223,2 440,2 440,20 208,20" fill="var(--brand-green)"/>
    </svg>
  </section>

  <section class="card card-back">
    <div class="back-wordmark"><span class="brand-dot-light"></span>THE STONEBRACE CO.</div>
    <div class="tagline">CRUSHING SOLUTIONS</div>
  </section>
</body>
</html>
```